Website images and banners needed to be created

We have a website we have not used in a few months that need updated sales banners and images resized for our web devs to upload and update. The site in question is w w w . p a l t r o n . c o m

Number of Pages Required

3 page

```html
<!DOCTYPE html>
<html lang="en">
<head>
<meta charset="utf-8">
<title>Paltron web banners</title>
<link rel="stylesheet" href="https://fonts.googleapis.com/css2?family=Montserrat:wght@300;400;500;600;800&family=Nunito:wght@600;700&display=swap">
<style>
  :root {
    --board: #666666;
    --white: #ffffff;
    --ink: #111111;
    --accent-yellow: #fcc70a;
    --room-dark: #1e1e20;
    --room-floor: #8f8e8e;
    --room-wood: #8e6d4f;
    --bed-cream: #eeeadb;
    --linen-light: #f1f3f5;
    --linen-mid: #dde2e7;
    --skin-warm: #e9c3a6;
    --hair-brown: #8a5a3c;
    --kids-pink: #f7507f;
    --kids-magenta: #ea5ea8;
    --kids-band: #e459a6;
    --kids-bed: #f5dbe7;
  }
  * { box-sizing: border-box; margin: 0; padding: 0; }
  html, body { width: 961px; height: 1200px; overflow: hidden; }
  body { background: var(--board); font-family: "Montserrat", sans-serif; position: relative; }

  .banner { position: absolute; left: 44px; width: 853px; height: 348px; overflow: hidden; }
  .banner--offers { top: 31px; }
  .banner--fabric { top: 410px; }
  .banner--kids { top: 784px; }

  .photo { position: absolute; }

  /* Offers banner */
  .offers-room {
    inset: 0;
    background:
      linear-gradient(180deg, rgba(0,0,0,0) 58%, rgba(150,148,148,0.85) 100%),
      linear-gradient(90deg, var(--room-dark) 0%, #2c2c2e 46%, var(--room-wood) 46.5%, #80614a 75%, #6a4c33 100%);
  }
  .offers-bed {
    left: -10px; top: 55px; width: 540px; height: 275px;
    background: radial-gradient(ellipse at 55% 52%, #ffffff 0%, var(--bed-cream) 38%, rgba(215,212,195,0.55) 58%, rgba(215,212,195,0) 72%);
  }
  .offers-copy {
    position: absolute; left: 669px; top: 100px; transform: translateX(-50%);
    text-align: center; color: var(--white); white-space: nowrap;
  }
  .offers-kicker { font-weight: 400; font-size: 20px; letter-spacing: 3px; line-height: 30px; }
  .offers-headline { font-weight: 800; font-size: 35px; line-height: 44px; }
  .offers-sub { font-weight: 400; font-size: 24px; line-height: 36px; margin-top: 3px; }
  .btn-outline {
    display: inline-block; border: 1.5px solid var(--white); color: var(--white);
    font-size: 13px; font-weight: 500; text-align: center;
    width: 135px; height: 36px; line-height: 33px;
  }
  .offers-copy .btn-outline { margin-top: 19px; }

  /* Fabric banner */
  .fabric-linen {
    inset: 0;
    background: linear-gradient(100deg, var(--linen-mid) 0%, var(--linen-light) 40%, #ffffff 70%, #e9edf1 100%);
  }
  .fabric-sleeper {
    left: 300px; top: -20px; width: 580px; height: 390px;
    background:
      radial-gradient(ellipse 22% 24% at 56% 30%, rgba(138,90,60,0.75) 0%, rgba(138,90,60,0) 100%),
      radial-gradient(ellipse 34% 30% at 65% 48%, rgba(233,195,166,0.9) 0%, rgba(233,195,166,0) 100%),
      radial-gradient(ellipse 50% 45% at 45% 62%, #ffffff 0%, rgba(255,255,255,0) 100%);
  }
  .fabric-copy { position: absolute; left: 66px; top: 162px; }
  .fabric-line {
    font-weight: 600; font-size: 37px; line-height: 44px; color: var(--ink); letter-spacing: -0.3px;
  }
  .fabric-tag {
    display: inline-block; margin-top: 3px; background: var(--accent-yellow); color: var(--white);
    font-weight: 500; font-size: 33px; line-height: 48px; padding: 0 20px 0 18px;
  }

  /* Kids banner */
  .kids-backdrop {
    inset: 0;
    background: linear-gradient(180deg, var(--kids-pink) 0%, #f5598c 65%, var(--kids-magenta) 100%);
  }
  .kids-band { position: absolute; left: 0; top: 0; width: 853px; height: 348px; }
  .kids-bed-photo {
    left: 385px; top: 40px; width: 470px; height: 280px;
    background:
      radial-gradient(ellipse 46% 42% at 50% 55%, #ffffff 0%, var(--kids-bed) 55%, rgba(245,219,231,0.6) 78%, rgba(245,219,231,0) 100%);
  }
  .kids-copy {
    position: absolute; left: 215px; top: 117px; transform: translateX(-50%);
    text-align: center; color: var(--white); white-space: nowrap;
  }
  .kids-kicker { font-family: "Montserrat", sans-serif; font-weight: 500; font-size: 17px; letter-spacing: 2.6px; line-height: 24px; }
  .kids-headline { font-family: "Nunito", sans-serif; font-weight: 700; font-size: 33px; line-height: 38px; }
  .kids-copy .btn-outline { margin-top: 14px; font-family: "Nunito", sans-serif; font-weight: 600; font-size: 13px; width: 134px; }
</style>
</head>
<body>
  <section class="banner banner--offers">
    <div class="photo offers-room" role="img" aria-label="Modern bedroom with dark wall, wooden wardrobe and tiled floor"></div>
    <div class="photo offers-bed" role="img" aria-label="Cream upholstered bed with white mattress and side table"></div>
    <div class="offers-copy">
      <p class="offers-kicker">SPECIAL OFFERS</p>
      <p class="offers-headline">UP TO 70% OFF</p>
      <p class="offers-sub">ON ALL MATTRESSES</p>
      <span class="btn-outline">SHOP NOW</span>
    </div>
  </section>

  <section class="banner banner--fabric">
    <div class="photo fabric-linen" role="img" aria-label="White bed linen"></div>
    <div class="photo fabric-sleeper" role="img" aria-label="Woman sleeping on a white pillow under a duvet"></div>
    <div class="fabric-copy">
      <p class="fabric-line">FABRIC BEDS &amp;</p>
      <span class="fabric-tag">MATTRESSES</span>
    </div>
  </section>

  <section class="banner banner--kids">
    <div class="photo kids-backdrop" role="img" aria-label="Pink patterned background"></div>
    <svg class="kids-band" viewBox="0 0 853 348" aria-hidden="true">
      <path d="M0 278 C 120 270, 200 232, 300 226 S 480 248, 560 262 S 760 270, 853 262 L 853 348 L 0 348 Z" fill="var(--kids-band)"/>
    </svg>
    <div class="photo kids-bed-photo" role="img" aria-label="White and pink children's bed with drawers"></div>
    <div class="kids-copy">
      <p class="kids-kicker">WELCOME TO PALTRON</p>
      <p class="kids-headline">SPECIAL KIDS BEDS</p>
      <span class="btn-outline">SHOP NOW</span>
    </div>
  </section>
</body>
</html>
```